Mobile Web App Design for Wellness Company

We already do have a website design developed at this address:
http://new.meadowbalancellc.com/

We need mobile web design. Not a mobile application design. We need design for what visitors would see when they visit http://new.meadowbalancellc.com/ on their mobile phones.

Mobile Web App design need to be similar to design of the actual website, please check from the address.

We need design for below pages:
- Home
- Biodynamic Craniosacral Therapy
- Biodynamic Lymphatic Drainage
- Chi Gong
- Contact Us
- About Us

We want easy access and obvious locations for navigate and call functionality.

We put together a design for mobile already but it's not good. Feel free to take the content from the website and/or mobile web app we designed to show your design with the actual content.

Design files must be high quality. We want designer to encorporate header images for the actual website we placed into mobile pages. For example, there's a header photo for each services, when visited in mobile, we'd like those images to show up too.

Most important part of this design will be easy of use and minimalist mobile focused design.

Good Luck!

Industry/Entity Type

Health And Wellness

Number of Pages Required

5+ page

Requirements
Must have
• Most important part of this design will be easy of use and minimalist mobile focused design.
Nice to have
• New up to date looking calming design
Should not have
• Dark background color

```html
<!DOCTYPE html>
<html lang="en">
<head>
<meta charset="utf-8">
<title>Meadow Balance – Mobile Home</title>
<link rel="stylesheet" href="https://fonts.googleapis.com/css2?family=Great+Vibes&family=Noto+Serif:wght@400;700&family=Open+Sans:wght@600;700&display=swap">
<style>
  :root {
    --page-bg: #f3f5f7;
    --screen-bg: #ffffff;
    --brand-blue: #1f5f9f;
    --ring-blue: #5ba3d6;
    --bar-start: #14a3da;
    --bar-end: #2bbbe9;
    --white: #ffffff;
    --ink: #222222;
    --panel-blue: #e4f2fd;
    --panel-blue-deep: #cfe7fb;
    --sky-top: #2f6fc0;
    --sky-mid: #7fb0e0;
    --water: #2a5f9e;
    --skin: #c98f74;
    --shirt: #c9574c;
  }
  * { box-sizing: border-box; margin: 0; padding: 0; }
  html, body {
    width: 1200px; height: 1200px; overflow: hidden;
    background: var(--page-bg);
  }
  .screen {
    position: absolute; left: 253px; top: 9px;
    width: 694px; height: 1182px;
    background: var(--screen-bg);
    overflow: hidden;
  }
  /* header */
  .site-header { position: relative; height: 174px; }
  .brand-name {
    position: absolute; left: 0; right: 0; top: 52px;
    text-align: center;
    font-family: "Noto Serif", serif; font-weight: 400;
    font-size: 52px; color: var(--brand-blue); letter-spacing: 0.5px;
  }
  .social-link {
    position: absolute; left: 604px; top: 45px;
    width: 69px; height: 69px; border-radius: 50%;
    border: 3px solid var(--ring-blue);
  }
  /* call bar */
  .call-bar {
    position: relative; height: 68px;
    background: linear-gradient(90deg, var(--bar-start), var(--bar-end));
    display: flex; align-items: center;
  }
  .call-icon {
    width: 50px; height: 50px; margin-left: 6px;
    background: var(--white);
    display: flex; align-items: center; justify-content: center;
  }
  .call-text {
    margin-left: 17px;
    font-family: "Open Sans", sans-serif; font-weight: 700;
    font-size: 21px; color: var(--white);
  }
  .menu-toggle { position: absolute; right: 10px; top: 19px; }
  /* hero */
  .hero { position: relative; height: 481px; color: var(--white); text-align: center; }
  .hero-image {
    position: absolute; inset: 0;
    background: linear-gradient(180deg, var(--sky-top) 0%, var(--sky-mid) 45%, #9fc2e6 58%, var(--water) 78%, #1e4d86 100%);
  }
  .hero-content { position: relative; }
  .hero-title {
    position: absolute; left: 0; right: 0; top: 32px;
    font-family: "Great Vibes", cursive; font-size: 66px; font-weight: 400;
  }
  .hero-tagline {
    position: absolute; left: 0; right: 0; top: 122px;
    font-family: "Noto Serif", serif; font-weight: 700; font-size: 15px;
  }
  .hero-services {
    position: absolute; left: 0; right: 0; top: 164px;
    list-style: none;
    font-family: "Noto Serif", serif; font-size: 28px; line-height: 34px;
  }
  .hero-motto {
    position: absolute; left: 0; right: 0; top: 279px;
    font-family: "Noto Serif", serif; font-size: 18px;
  }
  .mail-pin { position: absolute; left: 313px; top: 330px; }
  .hero-email {
    position: absolute; left: 0; right: 0; top: 412px;
    font-family: "Noto Serif", serif; font-size: 26px;
  }
  /* services */
  .service-row { position: relative; height: 420px; display: flex; }
  .service-photo {
    width: 348px; height: 100%;
    background: linear-gradient(135deg, var(--shirt) 0%, var(--skin) 35%, #d9a98f 60%, var(--shirt) 100%);
  }
  .service-card {
    position: relative; flex: 1;
    background: var(--panel-blue); text-align: center;
  }
  .service-card::before {
    content: ""; position: absolute; left: -22px; top: 177px;
    border-style: solid; border-width: 22px 22px 22px 0;
    border-color: transparent var(--panel-blue) transparent transparent;
  }
  .service-title {
    margin-top: 50px;
    font-family: "Noto Serif", serif; font-weight: 400; font-size: 46px; color: var(--ink);
  }
  .service-text {
    margin: 22px auto 0; width: 290px;
    font-family: "Noto Serif", serif; font-size: 21.5px; line-height: 41px; color: var(--ink);
  }
  .service-more { display: block; margin: 26px auto 0; }
  .next-row { display: flex; height: 39px; }
  .next-card { width: 348px; background: var(--panel-blue-deep); }
  .next-photo { flex: 1; background: linear-gradient(90deg, #a9b79c, #e8ddd2); }
</style>
</head>
<body>
<main class="screen">
  <header class="site-header">
    <div class="brand-name">Meadow Balance</div>
    <a class="social-link" aria-label="Social page"></a>
  </header>

  <div class="call-bar">
    <span class="call-icon">
      <svg width="22" height="22" viewBox="0 0 24 24" aria-hidden="true">
        <path fill="#14a3da" d="M6.6 10.8a15.1 15.1 0 0 0 6.6 6.6l2.2-2.2c.3-.3.7-.4 1-.2 1.1.4 2.3.6 3.6.6.6 0 1 .4 1 1V20c0 .6-.4 1-1 1A17 17 0 0 1 3 4c0-.6.4-1 1-1h3.5c.6 0 1 .4 1 1 0 1.3.2 2.5.6 3.6.1.3 0 .7-.2 1z"/>
      </svg>
    </span>
    <span class="call-text">CALL US : 555-014-2290</span>
    <svg class="menu-toggle" width="46" height="32" viewBox="0 0 46 32" aria-label="Menu">
      <rect y="1" width="46" height="4" fill="#fff"/>
      <rect y="14" width="46" height="4" fill="#fff"/>
      <rect y="27" width="46" height="4" fill="#fff"/>
    </svg>
  </div>

  <section class="hero">
    <div class="hero-image" role="img" aria-label="Balanced stones resting on calm water under a blue sky"></div>
    <div class="hero-content">
      <h1 class="hero-title">Meadow Balance</h1>
      <p class="hero-tagline">Helping you rediscover your inner resources for wellness</p>
      <ul class="hero-services">
        <li>Biodynamic Craniosacral Therapy (BCST)</li>
        <li>Biodynamic Lymphatic Drainage (BLD)</li>
        <li>Chi Gong</li>
      </ul>
      <p class="hero-motto">Recover Restore Replenish</p>
      <svg class="mail-pin" width="68" height="80" viewBox="0 0 68 80" aria-hidden="true">
        <path d="M34 0a34 34 0 0 1 10 66.5L34 80 24 66.5A34 34 0 0 1 34 0z" fill="#fff"/>
        <rect x="19" y="24" width="30" height="21" rx="3" fill="none" stroke="#1f7fc8" stroke-width="3"/>
        <path d="M20 26l14 10 14-10" fill="none" stroke="#1f7fc8" stroke-width="3"/>
      </svg>
      <p class="hero-email">info@meadowbalancellc.com</p>
    </div>
  </section>

  <section class="service-row">
    <div class="service-photo" role="img" aria-label="Client resting during a craniosacral therapy session"></div>
    <div class="service-card">
      <h2 class="service-title">BCST</h2>
      <p class="service-text">Rebalance your nervous system and get in touch with the health you were born with.</p>
      <svg class="service-more" width="34" height="16" viewBox="0 0 34 16" aria-label="Read more">
        <path d="M0 8h28" stroke="#222" stroke-width="3"/>
        <path d="M22 2l10 6-10 6z" fill="#222"/>
      </svg>
    </div>
  </section>

  <div class="next-row">
    <div class="next-card"></div>
    <div class="next-photo" role="img" aria-label="Lymphatic drainage treatment photo"></div>
  </div>
</main>
</body>
</html>
```